Corvex Hiring Partners Business Cards

Business cards with logo design for a new recruiting company called "Corvex Hiring Partners"

incorporate RED & BLUE colors

Final design should reflect strength - clean, elegant design

Company name superimposed upon graphic (Greek Columns)

Please see attached Photos!!!

Industry/Entity Type

Business

Font styles to use
Decorative

Colors
ec2027
0555a3
85cae6

Requirements
Must have
• Must look very similar to attached design!!!

Want Company name superimposed upon graphic (Greek Columns)

Tag line at bottom must be included:
"Strength in Every Team We Build and Every Hire We Make"

```html
<!DOCTYPE html>
<html lang="en">
<head>
<meta charset="utf-8">
<title>Corvex Hiring Partners – Business Card</title>
<link rel="stylesheet" href="https://fonts.googleapis.com/css2?family=Crimson+Text:wght@400;600&display=swap">
<style>
  :root {
    --brand-red: #ec2027;
    --brand-blue: #0555a3;
    --brand-sky: #85cae6;
    --ink: #1a1a1a;
    --card: #ffffff;
    --backdrop: #e9e6e2;
    --stone-light: #f4f5f7;
    --stone-mid: #e3e6ea;
    --mark-grey: #9aa1aa;
    --pill-light: #f3f5f9;
    --pill-edge: #e2e6ee;
  }
  * { box-sizing: border-box; margin: 0; padding: 0; }
  html, body { width: 1200px; height: 845px; overflow: hidden; }
  body {
    background: var(--backdrop);
    font-family: "Crimson Text", Georgia, serif;
    color: var(--ink);
  }
  .business-card {
    position: absolute;
    left: 80px;
    top: 125px;
    width: 1040px;
    height: 594px;
    background: var(--card);
    box-shadow: 0 10px 30px rgba(0,0,0,0.18);
    overflow: hidden;
  }
  .brand {
    position: absolute;
    left: 56px;
    top: 42px;
    width: 380px;
    height: 210px;
  }
  .brand-mark {
    position: absolute;
    left: 0;
    top: 78px;
    width: 54px;
    height: 54px;
    border-radius: 50%;
    background: var(--mark-grey);
  }
  .brand-columns {
    position: absolute;
    z-index: 0;
    left: 110px;
    top: 40px;
    width: 190px;
    height: 168px;
    background: linear-gradient(180deg, var(--stone-light), var(--stone-mid));
    border-radius: 4px;
  }
  .brand-name {
    position: absolute;
    z-index: 1;
    left: 84px;
    top: 0;
    font-size: 54px;
    line-height: 62px;
    font-weight: 400;
    color: var(--brand-blue);
  }
  .corner-pill {
    position: absolute;
    right: 48px;
    top: 28px;
    width: 96px;
    height: 250px;
    border-radius: 48px;
    background: linear-gradient(180deg, var(--pill-light), var(--pill-edge));
    border: 1px solid var(--pill-edge);
  }
  .holder-name {
    position: absolute;
    left: 56px;
    top: 312px;
    font-size: 44px;
    font-weight: 400;
    color: var(--brand-blue);
    letter-spacing: 0.5px;
  }
  .contact-list {
    position: absolute;
    left: 58px;
    top: 420px;
    list-style: none;
    font-size: 25px;
    line-height: 40px;
  }
  .contact-list li { display: flex; align-items: center; gap: 12px; }
  .contact-icon { width: 24px; height: 24px; flex: none; }
  .tagline {
    position: absolute;
    right: 60px;
    top: 300px;
    text-align: right;
    font-size: 36px;
    line-height: 44px;
    color: var(--brand-red);
  }
</style>
</head>
<body>
  <main class="business-card">
    <div class="corner-pill" aria-hidden="true"></div>

    <div class="brand">
      <span class="brand-mark"></span>
      <div class="brand-columns" role="img" aria-label="Greek columns graphic behind the company name"></div>
      <h1 class="brand-name">Corvex<br>Hiring<br>Partners</h1>
    </div>

    <p class="holder-name">Daniel R. Whitford</p>

    <ul class="contact-list">
      <li>
        <svg class="contact-icon" viewBox="0 0 24 24" aria-hidden="true">
          <circle cx="12" cy="12" r="10.5" fill="none" stroke="#1a1a1a" stroke-width="1.6"/>
          <path d="M8.5 6.5c1 0 1.3 2.3 1.3 2.3l-1 1c.6 1.6 1.8 2.8 3.4 3.4l1-1s2.3.3 2.3 1.3-1 2-2 2c-3.5 0-7-3.5-7-7 0-1 1-2 2-2z" fill="#1a1a1a"/>
        </svg>
        <span>512-555-0142</span>
      </li>
      <li>
        <svg class="contact-icon" viewBox="0 0 24 24" aria-hidden="true">
          <circle cx="12" cy="12" r="11.5" fill="#1a1a1a"/>
          <rect x="6" y="8" width="12" height="8.5" rx="1" fill="#fff"/>
          <path d="M6 8.5l6 4.5 6-4.5" fill="none" stroke="#1a1a1a" stroke-width="1.3"/>
        </svg>
        <span>DWhitford@CorvexHP.com</span>
      </li>
      <li>
        <svg class="contact-icon" viewBox="0 0 24 24" aria-hidden="true">
          <circle cx="12" cy="12" r="10.5" fill="none" stroke="#1a1a1a" stroke-width="1.6"/>
          <ellipse cx="12" cy="12" rx="4.5" ry="10.5" fill="none" stroke="#1a1a1a" stroke-width="1.4"/>
          <path d="M1.5 12h21M3.5 7h17M3.5 17h17" stroke="#1a1a1a" stroke-width="1.3"/>
        </svg>
        <span>www.CorvexHP.com</span>
      </li>
    </ul>

    <p class="tagline">Strength in<br>Every Team We Build<br>and Every Hire We Make</p>
  </main>
</body>
</html>
```